Business Card Design For A Cajun Seafood Restaurant

We are opening a cajun seafood restaurant in a week. We mainly serve cajun seafood which is orginally from Louisiana. We want design on both sides of a business card. I have menu on the website. You can go to www.reednkettle.example to check out our menu.

Restaurant name: Reed N' Kettle
Phone: +1 (555) 304-7712
Address: 48206 Ludlow Row, #7, Bexmoor Flats, Ca90000
Email: reednkettle@mailbox.example
Website: www.reednkettle.example

Maybe add social media icons (facebook, instagram) if looks nice on the business card.
facebook.com/reednkettle
instagram.com/reednkettle or @reednkettle

Attached is the logo and other business card samples that I like.

```html
<!DOCTYPE html>
<html lang="en">
<head>
<meta charset="utf-8">
<title>Reed N' Kettle – Business Card</title>
<link rel="stylesheet" href="https://fonts.googleapis.com/css2?family=PT+Sans:wght@400;700&display=swap">
<style>
  :root {
    --backdrop: #8c8c8c;
    --card: #f3f3f1;
    --accent: #e8601c;
    --ink: #4d4d4d;
    --ink-dark: #1e1e1e;
    --art-warm: #e07a2e;
    --art-gold: #e9b72a;
  }
  * { box-sizing: border-box; margin: 0; padding: 0; }
  html, body {
    width: 1105px; height: 1200px; overflow: hidden;
    background: var(--backdrop);
    font-family: "PT Sans", Arial, sans-serif;
    color: var(--ink);
  }
  .card {
    position: absolute; left: 179px;
    width: 747px; height: 425px;
    background: var(--card);
    overflow: hidden;
  }
  .card--front { top: 130px; }
  .card--back { top: 645px; }

  .mascot-art {
    position: absolute;
    border-radius: 50% 50% 42% 42%;
    background: radial-gradient(circle at 50% 30%, var(--art-gold) 0 22%, var(--art-warm) 48%, #c4531d 100%);
  }
  .card--front .mascot-art { left: 128px; top: 41px; width: 134px; height: 115px; }
  .card--back .mascot-art { left: 301px; top: 79px; width: 165px; height: 149px; }

  .brand-name {
    position: absolute;
    font-weight: 700;
    color: var(--ink-dark);
    letter-spacing: 1px;
    white-space: nowrap;
  }
  .card--front .brand-name { left: 46px; top: 158px; font-size: 30px; }
  .card--back .brand-name { left: 0; right: 0; top: 236px; text-align: center; font-size: 46px; }

  .rule {
    position: absolute; left: 328px; top: 193px;
    width: 377px; height: 2px; background: var(--ink-dark);
  }
  .accent-tab {
    position: absolute; right: 0; top: 135px;
    width: 15px; height: 49px; background: var(--accent);
  }
  .holder {
    position: absolute; right: 42px; top: 132px; text-align: right;
  }
  .holder__name { font-size: 26px; font-weight: 700; color: var(--accent); line-height: 1; }
  .holder__role { font-size: 19px; color: var(--ink-dark); margin-top: 3px; }

  .contact-list {
    position: absolute; left: 46px; top: 303px; list-style: none;
  }
  .contact-list li {
    display: flex; align-items: center; height: 29px;
    font-size: 19px;
  }
  .contact-list svg { width: 17px; height: 17px; margin-right: 10px; fill: var(--accent); }

  .address {
    position: absolute; right: 42px; top: 331px;
    text-align: right; font-size: 19px; line-height: 29px; font-style: normal;
  }

  .social-row {
    position: absolute; left: 0; right: 0; top: 360px;
    display: flex; justify-content: center; gap: 14px;
    font-size: 20px; color: var(--ink-dark);
  }
  .social-row span { display: flex; align-items: center; }
  .social-row span::before {
    content: ""; width: 24px; height: 24px; border-radius: 50%;
    background: var(--accent); margin-right: 6px;
  }
</style>
</head>
<body>
  <section class="card card--front">
    <div class="mascot-art" role="img" aria-label="Cartoon seafood mascot illustration"></div>
    <div class="brand-name">REED N' KETTLE</div>
    <div class="rule"></div>
    <div class="holder">
      <div class="holder__name">DANA WHITLOW</div>
      <div class="holder__role">CEO/Founder</div>
    </div>
    <div class="accent-tab"></div>
    <ul class="contact-list">
      <li>
        <svg viewBox="0 0 24 24" aria-hidden="true"><path d="M6.6 10.8a15.1 15.1 0 0 0 6.6 6.6l2.2-2.2a1 1 0 0 1 1-.25 11.4 11.4 0 0 0 3.6.57 1 1 0 0 1 1 1V20a1 1 0 0 1-1 1A17 17 0 0 1 3 4a1 1 0 0 1 1-1h3.5a1 1 0 0 1 1 1c0 1.25.2 2.45.57 3.57a1 1 0 0 1-.25 1z"/></svg>
        +1 (555) 304-7712
      </li>
      <li>
        <svg viewBox="0 0 24 24" aria-hidden="true"><path d="M2 5h20v14H2z M3 6l9 7 9-7" fill="none" stroke="var(--accent)" stroke-width="0"/><path d="M2 5h20v2l-10 7L2 7z"/><path d="M2 9l10 7 10-7v10H2z"/></svg>
        reednkettle@mailbox.example
      </li>
      <li>
        <svg viewBox="0 0 24 24" aria-hidden="true"><circle cx="12" cy="12" r="10"/><path d="M2 12h20M12 2c3 3 3 17 0 20M12 2c-3 3-3 17 0 20" fill="none" stroke="var(--card)" stroke-width="1.5"/></svg>
        www.reednkettle.example
      </li>
    </ul>
    <address class="address">
      48206 Ludlow Row, #7<br>
      Bexmoor Flats, Ca90000
    </address>
  </section>

  <section class="card card--back">
    <div class="mascot-art" role="img" aria-label="Cartoon seafood mascot illustration"></div>
    <div class="brand-name">REED N' KETTLE</div>
    <div class="social-row">
      <span>reednkettle</span>
      <span>@reednkettle</span>
    </div>
  </section>
</body>
</html>
```